Heritage Hollow Business Cards

Require a business card design. <br/><br/>Needs to include logo (either round or long version) plus these details:<br/>Maya Torvell<br/>Heritage Hollow<br/>maya@kelvadtrading.com.au<br/>02 6481 7395<br/>PO Box Glenwarra NSW 2791<br/>www.heritagehollow.com.au<br/><br/>I need in an editable format so that I can create for multiple staff members. <br/><br/>

Target Market(s)

We are an online store selling renovation products to home owners are builders. Looking for a classic classy design.

Industry/Entity Type

Home And Garden

Contact Information for Business Card

Maya Torvell
Heritage Hollow
maya@kelvadtrading.com.au
02 6481 7395
PO Box Glenwarra NSW 2791
www.heritagehollow.com.au

Colors

Designer to choose colors to be used in the design.

Requirements
Must have
• Must include Logo.

```html
<!DOCTYPE html>
<html lang="en">
<head>
<meta charset="utf-8">
<title>Heritage Hollow Business Cards</title>
<link rel="stylesheet" href="https://fonts.googleapis.com/css2?family=Montserrat:wght@400;600;700&display=swap">
<style>
  :root {
    --stage: #1e1e1e;
    --card-black: #070707;
    --card-white: #ffffff;
    --ink: #141414;
    --sage: #536e5f;
    --sage-text: #d6ded9;
    --contact: #ffffff;
    --line-light: #d8d8d8;
  }
  * { box-sizing: border-box; margin: 0; padding: 0; }
  html, body { width: 1200px; height: 900px; overflow: hidden; }
  body {
    background: var(--stage);
    font-family: "Montserrat", sans-serif;
    position: relative;
  }
  .card {
    position: absolute;
    left: 270px;
    width: 660px;
    height: 400px;
    overflow: hidden;
    box-shadow: 0 14px 30px rgba(0,0,0,0.45);
  }
  .card-back { top: 36px; background: var(--card-black); }
  .card-front { top: 464px; background: var(--card-white); }

  .roof-artwork {
    position: absolute;
    left: 60px; top: 90px;
    width: 520px; height: 230px;
    background: radial-gradient(ellipse at 55% 40%, rgba(90,90,90,0.28), rgba(20,20,20,0) 70%);
  }
  .brand-mark {
    position: absolute;
    width: 200px; height: 200px;
    border-radius: 50%;
    display: flex; align-items: center; justify-content: center;
    text-align: center;
    font-weight: 600;
    font-size: 26px;
    line-height: 1.1;
  }
  .card-back .brand-mark {
    left: 330px; top: 90px;
    border: 1.5px solid var(--line-light);
    color: var(--card-white);
  }
  .card-front .brand-mark {
    left: 40px; top: 20px;
    width: 170px; height: 170px;
    font-size: 23px;
    border: 1.5px solid var(--ink);
    color: var(--ink);
  }
  .staff-name {
    position: absolute;
    right: 48px; top: 112px;
    font-size: 30px;
    font-weight: 700;
    color: var(--ink);
    letter-spacing: 0.5px;
  }
  .wave { position: absolute; left: 0; top: 0; width: 660px; height: 400px; }
  .contact {
    position: absolute;
    right: 28px; top: 250px;
    text-align: right;
    font-size: 16px;
    line-height: 22px;
    color: var(--contact);
  }
  .contact .address { color: var(--sage-text); margin-bottom: 10px; }
  .contact-row { display: flex; justify-content: flex-end; align-items: center; gap: 8px; }
  .contact-row svg { width: 16px; height: 16px; flex: none; }
</style>
</head>
<body>
  <section class="card card-back">
    <div class="roof-artwork" role="img" aria-label="Faint sketched roof gable with chimney"></div>
    <div class="brand-mark">Heritage<br>Hollow</div>
  </section>

  <section class="card card-front">
    <svg class="wave" viewBox="0 0 660 400" aria-hidden="true">
      <path d="M0 300 C 190 240 420 262 660 214 L660 400 L0 400 Z" fill="var(--sage)"/>
      <path d="M0 262 C 180 212 420 240 660 196 L660 206 C 420 252 190 236 0 286 Z" fill="var(--ink)"/>
      <path d="M320 222 C 420 198 520 190 640 188 C 540 196 430 208 320 226 Z" fill="var(--ink)"/>
    </svg>

    <div class="brand-mark">Heritage<br>Hollow</div>
    <h1 class="staff-name">Maya Torvell</h1>

    <div class="contact">
      <p class="address">PO Box Glenwarra<br>NSW 2791</p>
      <p class="contact-row">02 6481 7395
        <svg viewBox="0 0 16 16"><circle cx="8" cy="8" r="7" fill="none" stroke="currentColor" stroke-width="1.3"/><path d="M5.5 4.5 L7 6 L6.2 7 C6.8 8.3 7.7 9.2 9 9.8 L10 9 L11.5 10.5 L10.6 11.6 C7.5 11.2 4.8 8.5 4.4 5.4 Z" fill="currentColor"/></svg>
      </p>
      <p class="contact-row">maya@kelvadtrading.com.au
        <svg viewBox="0 0 16 16"><rect x="1.5" y="3.5" width="13" height="9" fill="none" stroke="currentColor" stroke-width="1.3"/><path d="M1.5 3.5 L8 9 L14.5 3.5" fill="none" stroke="currentColor" stroke-width="1.3"/></svg>
      </p>
      <p class="contact-row">www.heritagehollow.com.au
        <svg viewBox="0 0 16 16"><circle cx="8" cy="8" r="6.5" fill="none" stroke="currentColor" stroke-width="1.3"/><ellipse cx="8" cy="8" rx="3" ry="6.5" fill="none" stroke="currentColor" stroke-width="1.1"/><path d="M1.5 8 H14.5 M2.5 5 H13.5 M2.5 11 H13.5" stroke="currentColor" stroke-width="1"/></svg>
      </p>
    </div>
  </section>
</body>
</html>
```